Brimvale display card for Lockout On Marlow

we need to design a display card for an lockout on marlow gift card that will be selling in brimvale. I' attached the specs and our logo, our website is lockoutonmarlow.com.

the offer will be 2x $50.00 gift cards for $79.99.

i also prefer our logo with the black background.

```html
<!DOCTYPE html>
<html lang="en">
<head>
<meta charset="utf-8">
<title>Lockout On Marlow – Brimvale Display Card</title>
<link rel="stylesheet" href="https://fonts.googleapis.com/css2?family=Anton&family=Oswald:wght@400;500;600;700&display=swap">
<style>
  :root{
    --page:#e9e9ec;
    --card-dark:#1b1b20;
    --panel-blue:#1f3b4e;
    --panel-blue-deep:#17303f;
    --accent-blue:#2f8fd0;
    --white:#ffffff;
    --yellow:#f4cf4a;
    --red:#d8392a;
    --orange:#ec4b24;
    --pink:#e6177f;
    --photo-mine-a:#2a1d14;
    --photo-mine-b:#6b4a2a;
    --photo-heist-a:#3a0a08;
    --photo-heist-b:#a11d16;
    --photo-cabin-a:#1b2430;
    --photo-cabin-b:#7d8796;
  }
  *{box-sizing:border-box;margin:0;padding:0}
  html,body{width:1200px;height:900px;overflow:hidden;background:var(--page)}
  .canvas{position:relative;width:1200px;height:900px}
  .card{position:absolute;top:124px;width:504px;height:650px;background:var(--card-dark);border-radius:30px;overflow:hidden;color:var(--white);font-family:'Oswald',sans-serif}
  .card--front{left:88px}
  .card--back{left:612px}
  .hang-hole{position:absolute;top:10px;left:50%;width:46px;height:12px;margin-left:-23px;border-radius:6px;background:var(--page);z-index:5}
  .notice{position:absolute;font-size:8.5px;font-weight:600;line-height:1.25;text-transform:uppercase}
  .notice--tl{top:22px;left:24px;width:190px}
  .notice--tr{top:22px;left:300px;width:185px}
  .notice--bl{top:622px;left:24px;width:230px}
  .notice--br{top:622px;left:278px;width:215px}
  .rule{position:absolute;left:0;right:0;top:62px;height:4px;background:var(--white)}
  .panel{position:absolute;left:0;right:0;background:radial-gradient(circle at 55% 55%,var(--panel-blue) 0%,var(--panel-blue-deep) 70%,var(--card-dark) 100%)}
  .panel--front{top:70px;height:540px}
  .panel--back{top:0;height:650px}
  .offer{position:absolute;top:92px;left:164px;font-family:'Oswald',sans-serif;font-weight:600;line-height:1;text-align:center}
  .offer__qty{font-size:34px}
  .offer__qty sup{font-size:18px;color:var(--accent-blue);vertical-align:12px}
  .offer__label{display:block;font-size:18px;margin-top:4px;text-transform:uppercase}
  .offer__price{position:absolute;top:86px;left:298px;font-family:'Anton',sans-serif;font-size:62px;line-height:1}
  .offer__price sup{font-size:36px;color:var(--accent-blue);vertical-align:20px}
  .brand-name{position:absolute;top:186px;left:0;right:0;text-align:center;font-family:'Anton',sans-serif;font-weight:400;font-size:84px;line-height:.98;color:var(--white);text-transform:uppercase}
  .tagline{position:absolute;top:488px;left:0;right:0;text-align:center;font-size:27px;font-weight:500;letter-spacing:15px;line-height:1.45;text-transform:uppercase}
  .fpo{position:absolute;display:flex;flex-direction:column;align-items:center}
  .fpo__label{font-size:7px;margin-bottom:2px}
  .fpo__box{background:var(--pink);color:var(--white);font-weight:700;font-size:15px;padding:1px 8px;border:2px solid var(--white)}
  .card--front .fpo{top:574px;left:400px}
  .card--back .fpo{top:574px;left:380px}
  .photo{position:absolute;left:0;width:300px}
  .photo--mine{top:0;height:208px;background:linear-gradient(135deg,var(--photo-mine-a),var(--photo-mine-b) 55%,var(--photo-mine-a))}
  .photo--heist{top:214px;height:218px;background:linear-gradient(120deg,var(--photo-heist-b),var(--photo-heist-a) 70%)}
  .photo--cabin{top:438px;height:212px;background:linear-gradient(180deg,var(--photo-cabin-a),var(--photo-cabin-b) 80%,var(--photo-cabin-a))}
  .room-title{position:absolute;right:196px;text-align:right;font-family:'Oswald',sans-serif;font-weight:700;line-height:1;text-transform:uppercase;text-shadow:2px 2px 0 rgba(0,0,0,.55);z-index:2}
  .room-title--mine{top:64px;font-size:42px;color:var(--yellow)}
  .room-title--heist{top:274px;font-size:44px;color:var(--red)}
  .room-title--cabin{top:474px;font-size:38px;color:var(--orange)}
  .web{position:absolute;top:622px;left:28px;font-size:11px;font-weight:600;color:var(--yellow);z-index:2}
  .address{position:absolute;top:574px;left:212px;font-size:11px;font-weight:500;line-height:1.35;text-transform:uppercase;z-index:2}
  .steps{position:absolute;top:48px;left:326px;width:158px;list-style:none}
  .step{margin-bottom:22px;text-transform:uppercase}
  .step__title{font-size:21px;font-weight:700;line-height:1.15}
  .step__text{font-size:13.5px;font-weight:500;line-height:1.45}
</style>
</head>
<body>
<main class="canvas">

  <section class="card card--front">
    <span class="hang-hole"></span>
    <p class="notice notice--tl">To purchase this item, please take this card to the cash register and exchange for the quantity you wish to purchase.</p>
    <p class="notice notice--tr">Veuillez présenter cette carte à la caisse pour l'échanger contre le nombre d'articles que vous souhaitez acheter.</p>
    <div class="rule"></div>
    <div class="panel panel--front" role="img" aria-label="Soft blue background where a faint maze pattern sits"></div>
    <p class="offer"><span class="offer__qty">2 X <sup>$</sup>50</span><span class="offer__label">Gift cards for</span></p>
    <p class="offer__price"><sup>$</sup>79.99</p>
    <h1 class="brand-name">Lockout<br>On<br>Marlow</h1>
    <p class="tagline">Real Life<br>Escape Game</p>
    <div class="fpo"><span class="fpo__label">ITM./ART.</span><span class="fpo__box">F.P.O.</span></div>
    <p class="notice notice--bl">Do not remove this card from the warehouse.<br>This card has no monetary value.</p>
    <p class="notice notice--br">Ne pas sortir cette carte de l'entrepôt.<br>Cette carte n'a aucune valeur marchande.</p>
  </section>

  <section class="card card--back">
    <span class="hang-hole"></span>
    <div class="panel panel--back" role="img" aria-label="Soft blue background where a faint maze pattern sits"></div>
    <div class="photo photo--mine" role="img" aria-label="Photo of a dim, warm-lit themed escape room"></div>
    <div class="photo photo--heist" role="img" aria-label="Photo of a themed escape room in red light"></div>
    <div class="photo photo--cabin" role="img" aria-label="Photo of an aircraft cabin style room with seats"></div>
    <h2 class="room-title room-title--mine">Escape<br>The Old Mine</h2>
    <h2 class="room-title room-title--heist">Harbour<br>Heist</h2>
    <h2 class="room-title room-title--cabin">Summit Skies:<br>Cabin Flight</h2>
    <p class="web">WWW.LOCKOUTONMARLOW.COM</p>
    <p class="address">1250 Harlow Ave, Unit 4<br>Brookfield, ON<br>L4X 2B9</p>
    <ul class="steps">
      <li class="step"><h3 class="step__title">60 Minutes</h3><p class="step__text">Can you puzzle your way through and escape the room in 60 minutes?</p></li>
      <li class="step"><h3 class="step__title">Discover</h3><p class="step__text">Take a look around the room to discover hidden clues and hints.</p></li>
      <li class="step"><h3 class="step__title">Solve</h3><p class="step__text">Solve clever and interesting puzzles to progress through the game.</p></li>
      <li class="step"><h3 class="step__title">Escape</h3><p class="step__text">Work together to escape because no one makes it out alone!</p></li>
    </ul>
    <div class="fpo"><span class="fpo__label">ITM./ART.</span><span class="fpo__box">F.P.O.</span></div>
  </section>

</main>
</body>
</html>
```